Brand Identity Stationary Package

Hello I'm looking for a full branding package for my Property Management Company. I have a logo but looking to have the following
Business Card
Email signature
Facebook cover photo
Letterhead (word.doc)
#10 Envelope
Pocket Folder - link to 9x12 pocket folder design specs https://www.printorbit-example.ca/marketing-materials/presentation-folders
would like everything to match and be brand identifiable. The company looks after residential properties/apartments and some commercial properties. Attached is a zip of the files.
For Business Card
Name: Gareth Lindqvist
Position: Operations Manager
Number: 1 (555) 384-2917
Email: Gareth@harborkey-example.ca
Website: Harborkey-example.ca
Property Management

```html
<!DOCTYPE html>
<html lang="en">
<head>
<meta charset="utf-8">
<title>Harborkey Business Card</title>
<link href="https://fonts.googleapis.com/css2?family=Roboto:wght@400;500;700&display=swap" rel="stylesheet">
<style>
  :root {
    --stage: #121212;
    --card: #1e1e1f;
    --edge: #5f9a22;
    --green: #7db446;
    --white: #f2f2f2;
    --muted: #d6d6d6;
  }
  * { margin: 0; padding: 0; box-sizing: border-box; }
  html, body {
    width: 1200px;
    height: 884px;
    overflow: hidden;
    background: var(--stage);
    font-family: "Roboto", Arial, sans-serif;
  }
  .stage {
    width: 1200px;
    height: 884px;
    display: flex;
    align-items: center;
    justify-content: center;
  }
  .business-card {
    position: relative;
    width: 1050px;
    height: 600px;
    background: var(--card);
    border: 3px solid var(--edge);
    box-shadow: 0 20px 50px rgba(0,0,0,0.6);
  }
  .brand {
    position: absolute;
    top: 120px;
    left: 0;
    right: 0;
    text-align: center;
  }
  .brand-name {
    display: inline-flex;
    align-items: center;
    gap: 18px;
    font-weight: 700;
    font-size: 66px;
    letter-spacing: 6px;
    color: var(--white);
  }
  .brand-dot {
    width: 22px;
    height: 22px;
    background: var(--white);
  }
  .divider {
    position: absolute;
    top: 395px;
    left: 200px;
    right: 150px;
    height: 2px;
    background: linear-gradient(90deg, rgba(255,255,255,0) 0%, rgba(255,255,255,0.75) 55%, rgba(255,255,255,0) 100%);
  }
  .person {
    position: absolute;
    left: 150px;
    top: 310px;
  }
  .person-name {
    font-weight: 500;
    font-size: 36px;
    color: var(--green);
    text-transform: uppercase;
    line-height: 1.05;
  }
  .person-title {
    font-size: 30px;
    color: var(--white);
    line-height: 1.2;
  }
  .contacts {
    position: absolute;
    left: 210px;
    top: 418px;
    list-style: none;
  }
  .contact-item {
    display: flex;
    align-items: center;
    gap: 14px;
    font-size: 29px;
    color: var(--white);
    line-height: 1.3;
  }
  .contact-icon {
    width: 26px;
    height: 26px;
    flex: none;
    fill: none;
    stroke: var(--green);
    stroke-width: 2.4;
  }
  .company-address {
    position: absolute;
    right: 100px;
    top: 268px;
    text-align: right;
    font-style: normal;
  }
  .company-legal {
    font-weight: 700;
    font-size: 30px;
    color: var(--green);
    line-height: 1.25;
  }
  .address-line {
    font-size: 32px;
    color: var(--muted);
    line-height: 1.25;
  }
</style>
</head>
<body>
<main class="stage">
  <article class="business-card">
    <header class="brand">
      <div class="brand-name"><span class="brand-dot"></span>HARBORKEY</div>
    </header>

    <section class="person">
      <h1 class="person-name">Gareth Lindqvist</h1>
      <p class="person-title">Operations Manager</p>
    </section>

    <address class="company-address">
      <div class="company-legal">Harbor Key, Ltd</div>
      <div class="address-line">48 Alder Crest Lane</div>
      <div class="address-line">Lakeview, ON L0X 1Z7</div>
    </address>

    <div class="divider"></div>

    <ul class="contacts">
      <li class="contact-item">
        <svg class="contact-icon" viewBox="0 0 24 24"><path d="M6 3l3 4-2 2c1 3 4 6 7 7l2-2 4 3-2 4C10 21 3 14 2 5z" fill="var(--green)" stroke="none"/></svg>
        1 (555) 384-2917
      </li>
      <li class="contact-item">
        <svg class="contact-icon" viewBox="0 0 24 24"><rect x="2" y="5" width="20" height="14" fill="var(--green)" stroke="none"/><path d="M2 5l10 8 10-8" stroke="var(--card)" stroke-width="2"/></svg>
        Gareth@harborkey-example.ca
      </li>
      <li class="contact-item">
        <svg class="contact-icon" viewBox="0 0 24 24"><circle cx="12" cy="12" r="9.5"/><ellipse cx="12" cy="12" rx="4" ry="9.5"/><path d="M3 12h18"/></svg>
        www.harborkey-example.ca
      </li>
    </ul>
  </article>
</main>
</body>
</html>
```